Agriculture farming Hemp and CBD

The logo is in works with your company now, should be ready in a few days. We have our Domain (kestrelbrookhollow.com) We would like to see incorporated seed to growth, but not necessary. we would like to nature colors and some black and green. we have our farm and will be growing and selling HEMP and CBD we are based in the state of Virginia. Would like to incorporate the words pause, play, rewind if possible but not necessary.

Target Market(s)

20 years old to elderly

Coding

Coded - Design and coding required

Number of Pages Required

3 page

Font styles to use
Serif

Requirements
Must have
• I'm not sure on the must haves, we are open to any ideas, we would definitely like to see Hemp and CBD included, may the life cycle of seed to plant. We must have a pop up asking if you are 20 years old before they can enter our site and to view or purchase our product. I want the design to be totally different than what i uploaded.
Nice to have
• Would like to see natural colors as well as black and green
Should not have
• I want

```html
<!DOCTYPE html>
<html lang="en">
<head>
<meta charset="utf-8">
<title>Kestrel Brook Hollow — Hemp &amp; CBD Farm</title>
<link rel="stylesheet" href="https://fonts.googleapis.com/css2?family=Montserrat:wght@300;400;600;700;800&family=Open+Sans:wght@400;600;700&display=swap">
<style>
:root{
  --black:#0c0c0c;
  --bar:#2b2b2b;
  --green:#2f9a1c;
  --green-bright:#3fc21d;
  --green-dark:#1f6e12;
  --gold:#f2b705;
  --gold-light:#ffd21f;
  --brown:#4a2b19;
  --brown-dark:#3a2113;
  --blush:#e2d8d6;
  --cream:#f4f1ec;
  --ink:#1a1a1a;
  --grey:#666;
  --white:#fff;
}
*{margin:0;padding:0;box-sizing:border-box}
html,body{width:1200px;height:4900px;overflow:hidden}
body{position:relative;background:var(--white);font-family:"Open Sans",Arial,sans-serif;color:var(--ink)}
section,header,footer{position:absolute;left:0;width:1200px}
.abs{position:absolute}
h1,h2,h3,.brand{font-family:"Montserrat",Arial,sans-serif}
.btn{position:absolute;display:flex;align-items:center;justify-content:center;background:linear-gradient(180deg,var(--gold-light),var(--gold));color:var(--white);font-family:"Montserrat",Arial,sans-serif;font-weight:700;font-size:13px;letter-spacing:.5px}
.body-text{font-size:12.5px;line-height:21px;color:var(--grey)}

/* top bar + nav */
.topbar{top:0;height:42px;background:var(--bar);color:#ddd;font-size:11px}
.topbar .email{left:57px;top:13px}
.topbar .phone{right:65px;top:13px;font-weight:700;color:#fff}
.topbar b{color:#fff}
.nav{top:42px;height:91px;background:var(--black)}
.brand{color:var(--white);font-weight:700;font-size:26px;letter-spacing:-.5px}
.nav .brand{left:52px;top:29px}
.nav a{position:absolute;top:40px;color:#ddd;font-family:"Montserrat",Arial,sans-serif;font-size:11.5px;text-decoration:none}
.nav a.active{color:var(--green-bright)}
.nav a.active::after{content:"";position:absolute;left:0;right:0;top:20px;height:2px;background:var(--green-bright)}

/* hero */
.hero{top:133px;height:640px}
.hero-photo{position:absolute;inset:0;background:radial-gradient(ellipse at 55% 50%,#6b6a3e 0%,#3d3a24 40%,#1a1812 80%)}
.hero .welcome{left:0;width:1200px;top:150px;text-align:center;color:#fff;font-family:"Montserrat",Arial,sans-serif;font-weight:400;font-size:46px}
.hero .title{left:0;width:1200px;top:200px;text-align:center;color:#fff;font-weight:700;font-size:58px}
.hero .title span{color:var(--green-bright)}
.hero .btn{left:522px;top:294px;width:166px;height:44px}
.dots{left:570px;top:526px;display:flex;gap:12px}
.dots i{width:11px;height:11px;border-radius:50%;border:2px solid #fff}
.dots i.on{background:#fff}
.hub{width:64px;height:64px;border-radius:50%;background:var(--black)}

/* about */
.about{top:742px;height:586px;background:linear-gradient(180deg,#f1f1f3,#e4e4e8)}
.about-art{left:0;top:0;width:600px;height:586px;background:radial-gradient(circle at 45% 45%,#e9e9ec 0 28%,#8fb36a 29% 40%,#d9dbd7 60%)}
.about h2{left:637px;top:118px;font-size:36px;line-height:46px;font-weight:700;color:var(--ink)}
.about .body-text{left:635px;top:232px;width:490px}
.about .btn{left:633px;top:424px;width:164px;height:42px}

/* why */
.why{top:1328px;height:498px;background:radial-gradient(ellipse at 50% 40%,#3ca726,#2c8f18 70%)}
.why h2{left:0;width:1200px;top:78px;text-align:center;color:#fff;font-size:36px;font-weight:700}
.ring{left:382px;top:145px;width:420px;height:420px;border-radius:50%;border:1px solid rgba(255,255,255,.35)}
.leaf-disc{left:432px;top:204px;width:320px;height:320px;border-radius:50%;background:radial-gradient(circle,#2f7e1c,#174e0c)}
.feature{color:#fff}
.feature h3{font-size:15px;font-weight:600;letter-spacing:.3px}
.feature p{font-size:11.5px;color:rgba(255,255,255,.75);margin-top:3px}
.feature.r{text-align:right}
.badge{width:40px;height:40px;border-radius:50%;border:2px solid rgba(255,255,255,.85)}

/* product rows */
.hemp{top:1826px;height:540px;background:var(--blush)}
.hemp-photo{left:570px;top:0;width:630px;height:540px;background:radial-gradient(ellipse at 55% 60%,#c9b68a 0%,#a89064 35%,#d9d2cc 75%)}
.product h2{font-size:40px;font-weight:700}
.product .body-text{width:440px}
.product .body-text p+p{margin-top:16px}
.product .btn{width:164px;height:42px}
.controls{display:flex;gap:20px;align-items:center}
.cbd{top:2366px;height:546px;background:#fff}
.cbd-photo{left:0;top:0;width:656px;height:546px;background:radial-gradient(ellipse at 40% 50%,#d9b84a 0%,#6f9a3a 25%,#eaf0e4 65%,#fff 85%)}

/* testimonials */
.people{top:2912px;height:570px;background:radial-gradient(ellipse at 50% 50%,var(--brown),var(--brown-dark))}
.people h2{left:0;width:1200px;top:50px;text-align:center;color:#fff;font-size:36px;font-weight:700}
.card{top:188px;width:292px;height:263px;border:1px solid rgba(255,255,255,.55);color:rgba(255,255,255,.8);text-align:center;padding:70px 38px 0}
.card.featured{background:var(--green);border-color:var(--green);color:#fff}
.card p{font-size:11px;line-height:18px}
.card h4{margin-top:14px;font-size:10.5px;font-weight:700;color:#fff}
.avatar{top:137px;width:104px;height:104px;border-radius:50%;border:4px solid #fff;background:linear-gradient(160deg,#b08666,#6d4a33)}
.arrow{width:28px;height:28px;border-radius:50%;background:#fff;display:flex;align-items:center;justify-content:center}

/* blogs */
.blogs{top:3482px;height:562px;background:var(--cream)}
.blogs h2{left:124px;top:86px;font-size:36px;font-weight:700}
.post{top:161px;width:310px}
.post .thumb{width:310px;height:186px}
.post h3{margin-top:24px;font-size:16px;font-weight:600}
.post p{margin-top:6px;font-size:11.5px;line-height:15px;color:#444}
.post .more{margin-top:10px;font-size:10.5px;font-weight:700;font-family:"Montserrat",Arial,sans-serif}

/* contact */
.contact{top:4044px;height:560px;background:var(--green)}
.field-photo{left:0;top:0;width:603px;height:560px;background:linear-gradient(180deg,#9db0b8 0%,#7d9261 30%,#4a7a2a 60%,#2f5a1a 100%)}
.contact .eyebrow{left:690px;top:68px;color:#fff;font-family:"Montserrat",Arial,sans-serif;font-size:22px;font-weight:300}
.contact h2{left:688px;top:96px;color:#fff;font-size:33px;font-weight:700}
.input{left:692px;width:428px;height:46px;background:#fff;border-bottom:2px solid #ccc;font-size:13px;color:#666;padding:15px 18px}
.contact .send{left:692px;top:441px;width:130px;height:36px;border-radius:18px;background:#f8e7a2;color:var(--ink);font-size:12px}

/* footer */
footer{top:4560px;height:340px;background:var(--black)}
footer .curve{left:0;top:-1px}
footer .brand{left:0;width:1200px;top:110px;text-align:center;font-size:30px}
.footer-nav a{position:absolute;top:183px;color:#fff;font-family:"Montserrat",Arial,sans-serif;font-size:11.5px;font-weight:600;text-decoration:none}
.copy{left:0;width:1200px;top:212px;text-align:center;color:#bbb;font-size:11px}
.social{width:30px;height:30px;border-radius:50%;background:var(--green-bright);top:248px}
</style>
</head>
<body>

<header class="topbar">
  <div class="abs email"><svg width="14" height="10" viewBox="0 0 14 10" style="vertical-align:-1px;margin-right:8px"><rect x=".5" y=".5" width="13" height="9" fill="#fff"/><path d="M1 1l6 5 6-5" stroke="#2b2b2b" fill="none"/></svg><b>Email us:</b> hello@kestrelbrookhollow.com</div>
  <div class="abs phone"><svg width="11" height="11" viewBox="0 0 24 24" style="vertical-align:-1px;margin-right:4px"><path fill="#fff" d="M6.6 10.8a15 15 0 006.6 6.6l2.2-2.2c.3-.3.7-.4 1-.2 1.1.4 2.3.6 3.6.6.6 0 1 .4 1 1V20c0 .6-.4 1-1 1A17 17 0 013 4c0-.6.4-1 1-1h3.5c.6 0 1 .4 1 1 0 1.3.2 2.5.6 3.6.1.3 0 .7-.2 1z"/></svg>Call Today: (555) 014 2290</div>
</header>

<nav class="nav" style="position:absolute;left:0;width:1200px">
  <div class="abs brand">kestrelbrookhollow.com</div>
  <a class="active" style="left:496px">HOME</a>
  <a style="left:582px">ABOUT US</a>
  <a style="left:689px">CBD</a>
  <a style="left:761px">HEMP</a>
  <a style="left:843px">BLOGS</a>
  <a style="left:928px">RESOURCES</a>
  <a style="left:1046px">CONTACT US</a>
</nav>

<section class="hero">
  <div class="hero-photo" role="img" aria-label="Close-up of dried hemp flower spilling from a glass jar"></div>
  <div class="abs welcome">Welcome to</div>
  <h1 class="abs title">The <span>Kestrel Brook Hollow</span></h1>
  <div class="btn">CONTACT US &nbsp;›</div>
  <div class="abs dots"><i class="on"></i><i></i><i></i></div>
</section>

<section class="about">
  <svg class="abs" style="left:0;top:-30px" width="1200" height="60" viewBox="0 0 1200 60"><path d="M0 30 Q600 -10 1200 40 V60 H0Z" fill="#f1f1f3"/></svg>
  <div class="abs about-art" role="img" aria-label="Hemp leaves, oil dropper bottles and a seed-to-plant growth cycle around a white plate"></div>
  <h2 class="abs">About The Kestrel<br>Brook Hollow</h2>
  <div class="abs body-text">Curabitur vel dolor ultrices ipsum dictum tristique Praesent vitae lacus Ut velit enim vestibulum non fermentum nec hendrerit quis leo Pellentesque rutrum malesuada neque Nunc tempus felis vitae urna Vivamus porttitor neque at volutpat rutrum purus nisi eleifend libero a tempus libero lectus feugiat felis Morbi diam mauris viverra in gravida eu mattis in anquam Curabitur vel dolor ultrices ipsum dictum tristique Praesent vitae lacus Ut velit enim</div>
  <div class="btn">LEARN MORE</div>
</section>

<div class="abs hub" style="left:568px;top:690px;z-index:2"></div>

<section class="why">
  <h2 class="abs">Why Choose Us</h2>
  <div class="abs ring"></div>
  <div class="abs leaf-disc" role="img" aria-label="Hemp leaf texture inside a round emblem"></div>

  <div class="abs feature r" style="right:790px;top:195px"><h3>VAGAN</h3><p>Lorem ipsum dolor sit amet consectet</p></div>
  <div class="abs badge" style="left:438px;top:184px"></div>

  <div class="abs badge" style="left:708px;top:194px"></div>
  <div class="abs feature" style="left:786px;top:195px"><h3>NO GMO 3RD PARTY TESTED</h3><p>Lorem ipsum dolor sit amet consectet</p></div>

  <div class="abs feature r" style="right:848px;top:366px"><h3>GLUTEN FREE</h3><p>Lorem ipsum dolor sit amet consect</p></div>
  <div class="abs badge" style="left:372px;top:362px"></div>

  <div class="abs badge" style="left:783px;top:362px"></div>
  <div class="abs feature" style="left:842px;top:366px"><h3>FARM BILL COMPLIANT</h3><p>Lorem ipsum dolor sit amet consectet</p></div>
</section>

<section class="hemp product">
  <div class="abs hemp-photo" role="img" aria-label="Hemp seed oil bottle beside a wooden bowl of hemp powder and a scoop of seeds on burlap"></div>
  <h2 class="abs" style="left:129px;top:118px">Selling Hemp</h2>
  <div class="abs body-text" style="left:129px;top:190px">
    <p>Curabitur vel dolor ultrices ipsum dictum tristique Praesent vitae lacus Ut velit enim vestibulum non fermentum nec hendrerit quis leo Pellentesque rutrum malesuada neque Nunc tempus felis vitae urna Vivamus porttitor neque at volutpat rutrum purus nisi eleifend libero</p>
    <p>Morbi diam mauris viverra in gravida eu mattis in anquam Curabitur vel dolor ultrices ipsum dictum tristique Praesent vitae lacus Ut velit enim</p>
  </div>
  <div class="btn" style="left:129px;top:358px">SHOP NOW</div>
  <div class="abs controls" style="left:127px;top:428px" aria-label="rewind, play, pause">
    <svg width="20" height="12" viewBox="0 0 20 12"><path d="M10 0v12L0 6zM20 0v12L10 6z" fill="#222"/></svg>
    <svg width="10" height="12" viewBox="0 0 10 12"><path d="M0 0l10 6-10 6z" fill="#222"/></svg>
    <svg width="12" height="12" viewBox="0 0 12 12"><rect width="4" height="12" fill="#222"/><rect x="8" width="4" height="12" fill="#222"/></svg>
  </div>
</section>

<section class="cbd product">
  <div class="abs cbd-photo" role="img" aria-label="Glass bottle of CBD oil against a large hemp leaf"></div>
  <h2 class="abs" style="left:670px;top:122px">CBD Oil</h2>
  <div class="abs body-text" style="left:668px;top:186px">
    <p>Curabitur vel dolor ultrices ipsum dictum tristique Praesent vitae lacus Ut velit enim vestibulum non fermentum nec hendrerit quis leo Pellentesque rutrum malesuada neque Nunc tempus felis vitae urna Vivamus porttitor neque at volutpat rutrum purus nisi eleifend libero</p>
    <p>Morbi diam mauris viverra in gravida eu mattis in anquam Curabitur vel dolor ultrices ipsum dictum tristique Praesent vitae lacus Ut velit enim</p>
  </div>
  <div class="btn" style="left:668px;top:357px">SHOP NOW</div>
  <div class="abs controls" style="left:672px;top:438px" aria-label="rewind, play, pause">
    <svg width="20" height="12" viewBox="0 0 20 12"><path d="M10 0v12L0 6zM20 0v12L10 6z" fill="#222"/></svg>
    <svg width="10" height="12" viewBox="0 0 10 12"><path d="M0 0l10 6-10 6z" fill="#222"/></svg>
    <svg width="12" height="12" viewBox="0 0 12 12"><rect width="4" height="12" fill="#222"/><rect x="8" width="4" height="12" fill="#222"/></svg>
  </div>
</section>

<section class="people">
  <h2 class="abs">What People Says</h2>
  <div class="abs arrow" style="left:80px;top:305px"><svg width="8" height="10" viewBox="0 0 8 10"><path d="M6 1L2 5l4 4" stroke="#333" stroke-width="1.6" fill="none"/></svg></div>
  <div class="abs arrow" style="left:1099px;top:298px"><svg width="8" height="10" viewBox="0 0 8 10"><path d="M2 1l4 4-4 4" stroke="#333" stroke-width="1.6" fill="none"/></svg></div>

  <div class="abs card" style="left:135px"><p>Augiat in pede Fusce tellus Sed metus augue convallis et vehicula ut pulvinar eu ante Integer orci tellus trisAultricies orci ac feugiat suscipit leo massa sodales velit et scelerisque mi tortor at ipsum Proin orci odio commodo ac gravida non tristique vel</p><h4>JOHN DEO</h4></div>
  <div class="abs card featured" style="left:453px"><p>Augiat in pede Fusce tellus Sed metus augue convallis et vehicula ut pulvinar eu ante Integer orci tellus trisAultricies orci ac feugiat suscipit leo massa sodales velit et scelerisque mi tortor at ipsum Proin orci odio commodo ac gravida non tristique vel</p><h4>JOHN DEO</h4></div>
  <div class="abs card" style="left:768px"><p>Augiat in pede Fusce tellus Sed metus augue convallis et vehicula ut pulvinar eu ante Integer orci tellus trisAultricies orci ac feugiat suscipit leo massa sodales velit et scelerisque mi tortor at ipsum Proin orci odio commodo ac gravida non tristique vel</p><h4>JOHN DEO</h4></div>

  <div class="abs avatar" style="left:229px" role="img" aria-label="Customer portrait"></div>
  <div class="abs avatar" style="left:547px" role="img" aria-label="Customer portrait"></div>
  <div class="abs avatar" style="left:862px" role="img" aria-label="Customer portrait"></div>
</section>

<section class="blogs">
  <h2 class="abs">Latest Blogs</h2>
  <article class="abs post" style="left:116px">
    <div class="thumb" role="img" aria-label="CBD cream jar with dropper bottles and a hemp leaf" style="background:linear-gradient(135deg,#e8ece6,#a9c79b 55%,#d9a34a)"></div>
    <h3>Lorem ipsum blog heading</h3>
    <p>Augiat in pede Fusce tellus Sed metus augue con-vallis et vehicula ut pulvinar eu ante</p>
    <div class="more">LEARN MORE</div>
  </article>
  <article class="abs post" style="left:455px">
    <div class="thumb" role="img" aria-label="Hemp plant leaves in sunlight" style="background:radial-gradient(circle at 50% 50%,#9fd05a,#3d7a1e 70%)"></div>
    <h3>Lorem ipsum blog heading</h3>
    <p>Augiat in pede Fusce tellus Sed metus augue con-vallis et vehicula ut pulvinar eu ante</p>
    <div class="more">LEARN MORE</div>
  </article>
  <article class="abs post" style="left:790px">
    <div class="thumb" role="img" aria-label="CBD oil bottles and capsules on a table with hemp plants behind" style="background:linear-gradient(180deg,#6e9a3e,#a5b56a 55%,#d9c48a)"></div>
    <h3>Lorem ipsum blog heading</h3>
    <p>Augiat in pede Fusce tellus Sed metus augue con-vallis et vehicula ut pulvinar eu ante</p>
    <div class="more">LEARN MORE</div>
  </article>
</section>

<section class="contact">
  <div class="abs field-photo" role="img" aria-label="Hemp field in front of misty mountains"></div>
  <div class="abs eyebrow">Contact Form</div>
  <h2 class="abs">Get in touch with us</h2>
  <div class="abs input" style="top:167px">Name*</div>
  <div class="abs input" style="top:222px">Email *</div>
  <div class="abs input" style="top:276px">Phone*</div>
  <div class="abs input" style="top:331px;height:86px">Message</div>
  <div class="btn send">SEND &nbsp;›</div>
</section>

<footer>
  <svg class="abs curve" width="1200" height="50" viewBox="0 0 1200 50"><path d="M0 0 H1200 V6 Q900 30 600 40 Q300 34 0 20Z" fill="#2f9a1c"/><path d="M0 0 H603 V38 Q300 34 0 20Z" fill="#2f5a1a"/></svg>
  <div class="abs hub" style="left:568px;top:10px;border:2px solid #222"></div>
  <div class="abs brand">kestrelbrookhollow.com</div>
  <div class="footer-nav">
    <a style="left:265px">HOME</a>
    <a style="left:350px">ABOUT US</a>
    <a style="left:462px">PRODUCTS</a>
    <a style="left:574px">SHOP</a>
    <a style="left:652px">BLOGS</a>
    <a style="left:738px">TESTIMONIALS</a>
    <a style="left:874px">CONTACT</a>
  </div>
  <div class="abs copy">© Copyright 2020 . Kestrel Brook Hollow . All Right Reserved</div>
  <div class="abs social" style="left:527px"></div>
  <div class="abs social" style="left:565px"></div>
  <div class="abs social" style="left:603px"></div>
  <div class="abs social" style="left:641px"></div>
</footer>

</body>
</html>
```